Alloy wheel repair business needs a website

Install logo previously purchased from makerhive, toolbar with dropdowns. services, gallery, clients , contact ect
Maybe mission statment

Target Market(s)

vehicle owners, auto dealers,insurance companies,

Industry/Entity Type

Alloy Wheel Repair

Coding

Coded - Design and coding required

Number of Pages Required

4 page

Font styles to use
Sans Serif

Colors
0054AA
0677BA
7BADD7
CADEEF
E8F1F8

```html
<!DOCTYPE html>
<html lang="en">
<head>
<meta charset="utf-8">
<title>Rimwell Works – Alloy Wheel Repair Specialists</title>
<link rel="stylesheet" href="https://fonts.googleapis.com/css2?family=Krona+One&family=Roboto:ital,wght@0,400;0,500;0,700;1,400&display=swap">
<style>
:root{
  --blue:#0054aa;
  --blue-mid:#0677ba;
  --blue-soft:#7badd7;
  --blue-pale:#cadeef;
  --blue-mist:#e8f1f8;
  --accent:#3f86d4;
  --navy:#0b2c5a;
  --navy-deep:#071d3e;
  --ink:#111418;
  --text:#2a2f36;
  --muted:#6b7078;
  --paper:#ffffff;
  --grey:#f2f2f2;
  --dark:#1b1d21;
  --star:#f5b301;
}
*{box-sizing:border-box;margin:0;padding:0}
html,body{width:1200px;height:5121px;overflow:hidden}
body{font-family:"Roboto",Arial,sans-serif;color:var(--text);background:var(--paper);position:relative}
.section{position:absolute;left:0;width:1200px}
.abs{position:absolute}
.display{font-family:"Krona One","Arial Black",sans-serif;font-style:normal;text-transform:uppercase;letter-spacing:1px;color:var(--ink)}
.eyebrow{font-family:"Roboto",Arial,sans-serif;font-weight:500;letter-spacing:4px;text-transform:uppercase;font-size:20px;color:var(--accent)}
.center{left:0;width:1200px;text-align:center}
.btn{position:absolute;display:flex;align-items:center;justify-content:center;background:var(--accent);color:#fff;font-family:"Krona One",sans-serif;font-size:11px;letter-spacing:1px;text-transform:uppercase;box-shadow:0 0 0 3px rgba(63,134,212,.35)}
.btn-outline{background:transparent;border:1.5px solid #fff;box-shadow:none}
.brand{font-family:"Krona One",sans-serif;color:var(--blue-mid);text-transform:uppercase}

/* header */
.site-header{top:0;height:76px;background:#fff}
.site-header .brand{left:123px;top:18px;font-size:26px;line-height:1}
.site-header .brand small{display:block;font-size:11px;color:var(--ink);letter-spacing:4px;margin-top:4px}
.nav{left:487px;top:39px;display:flex;gap:0;font-size:13px;font-weight:500;color:var(--ink)}
.nav span{position:absolute;white-space:nowrap}
.call{left:944px;top:28px}
.call .label{position:absolute;left:34px;top:0;font-size:12px;white-space:nowrap;color:var(--ink)}
.call .num{position:absolute;left:34px;top:18px;font-size:16px;font-weight:700;white-space:nowrap;color:var(--ink)}

/* hero */
.hero{top:76px;height:538px;background:#000}
.hero-photo{left:480px;top:0;width:720px;height:538px;background:linear-gradient(90deg,#000 0%,#2b2f35 30%,#6d7680 60%,#3a3f46 100%)}
.hero-welcome{left:123px;top:136px;color:#fff;font-family:"Krona One",sans-serif;font-size:20px;letter-spacing:4px}
.hero-brand{left:121px;top:170px;font-size:64px;line-height:1}
.hero-brand-sub{left:123px;top:262px;color:#fff;font-family:"Krona One",sans-serif;font-size:38px;letter-spacing:5px}
.hero-tag{left:119px;top:338px;color:#fff;font-size:18px;font-weight:500;letter-spacing:1px}

/* services */
.services{top:614px;height:712px;background:linear-gradient(180deg,#fff,#f6f7f8)}
.services .eyebrow{top:92px}
.services h2{top:132px;font-size:40px}
.card{position:absolute;top:207px;width:270px;height:326px;background:#fff;border-radius:6px;box-shadow:0 8px 24px rgba(0,0,0,.1);text-align:center}
.card svg{position:absolute;left:95px;top:24px}
.card h3{position:absolute;left:20px;right:20px;top:112px;font-size:17px;font-weight:500;letter-spacing:1.5px;line-height:25px;color:var(--ink);text-transform:uppercase}
.card p{position:absolute;left:28px;right:28px;top:184px;font-size:12.5px;line-height:21px;color:var(--muted);letter-spacing:.5px}
.card .more{position:absolute;left:0;right:0;top:290px;font-size:12px;font-weight:700;letter-spacing:1.5px;color:var(--accent)}
.card.featured{background:var(--navy-deep)}
.card.featured h3{color:#fff}
.card.featured p{color:#c9d4e4}

/* mission */
.mission{top:1326px;height:572px;background:linear-gradient(135deg,var(--navy) 0%,var(--navy-deep) 100%)}
.mission .eyebrow{top:76px;color:#fff}
.mission h2{top:114px;font-size:40px;color:#fff}
.point{position:absolute;top:219px;width:420px}
.point .tick{position:absolute;left:0;top:0;width:52px;height:52px;background:var(--accent);border-radius:4px}
.point h3{position:absolute;left:77px;top:6px;font-size:17px;font-weight:500;letter-spacing:1.5px;color:#fff;white-space:nowrap}
.point p{position:absolute;left:77px;top:44px;width:345px;font-size:12.5px;line-height:21px;color:#d3dbe7}
.mission-photo{left:161px;top:1739px;width:877px;height:394px;border-radius:14px;border:2px solid #fff;background:linear-gradient(90deg,#2d3035 0%,#5e646c 40%,#9aa0a8 55%,#3b3f45 100%);box-shadow:0 30px 40px -20px rgba(0,0,0,.45)}

/* gallery */
.gallery{top:1898px;height:1189px;background:var(--grey)}
.gallery .eyebrow{top:364px}
.gallery h2{top:408px;font-size:40px}
.tile{position:absolute;width:280px;height:267px;border-radius:4px}
.view-all{left:545px;top:1088px;font-family:"Krona One",sans-serif;font-size:12px;color:var(--accent);letter-spacing:1px;border-bottom:1.5px solid var(--accent);padding-bottom:4px}

/* quote */
.quote{top:3087px;height:430px;background:linear-gradient(135deg,var(--navy) 0%,var(--navy-deep) 100%)}
.quote .eyebrow{top:64px;color:#fff}
.quote h2{top:108px;font-size:40px;line-height:56px;color:#fff}
.quote .rule{left:568px;top:214px;width:64px;height:3px;background:var(--accent)}
.quote p{top:238px;font-size:17px;line-height:28px;font-weight:500;color:#fff;letter-spacing:.8px}

/* testimonials */
.testimonials{top:3517px;height:658px;background:#fff}
.testimonials .eyebrow{top:88px}
.testimonials h2{top:128px;font-size:40px}
.review{position:absolute;top:220px;width:270px;height:259px;background:#fff;box-shadow:0 6px 22px rgba(0,0,0,.1)}
.review .mark{position:absolute;left:26px;top:-20px;font-family:"Krona One",sans-serif;font-size:80px;line-height:1;color:var(--accent)}
.review p{position:absolute;left:26px;right:26px;top:52px;font-size:11.5px;line-height:20px;font-style:italic;color:var(--muted)}
.reviewer{position:absolute;top:510px}
.reviewer .avatar{position:absolute;left:0;top:0;width:38px;height:38px;border-radius:50%;background:linear-gradient(135deg,#6b5a4e,#2d2622)}
.reviewer .name{position:absolute;left:50px;top:2px;font-family:"Krona One",sans-serif;font-size:12px;color:var(--ink);white-space:nowrap}
.reviewer .stars{position:absolute;left:50px;top:18px;color:var(--star);font-size:15px;letter-spacing:2px;white-space:nowrap}
.dots{left:552px;top:593px}
.dots span{position:absolute;top:0;height:4px;width:28px;background:#d5d8dc}

/* contact */
.contact{top:4175px;height:538px;background:#1e2024}
.contact-photo{left:0;top:0;width:610px;height:538px;background:linear-gradient(90deg,#2a2d31 0%,#4d535a 55%,#232528 100%)}
.contact .eyebrow{left:640px;top:60px;color:#fff}
.contact h2{left:640px;top:108px;font-size:40px;line-height:56px;color:#fff}
.field{position:absolute;border-bottom:1px solid #6a6e74}
.field label{position:absolute;left:4px;font-size:13px;font-weight:700;color:#fff}
.field label em{color:#e04848;font-style:normal}

/* footer */
.footer{top:4713px;height:408px;background:linear-gradient(135deg,#1b1d21,#101214)}
.footer .brand{left:103px;top:88px;font-size:40px;line-height:1}
.footer .brand small{display:block;font-size:22px;color:#fff;letter-spacing:5px;margin-top:6px}
.footer .about{left:107px;top:197px;width:300px;font-size:12.5px;line-height:20px;color:#c9ccd1}
.social{position:absolute;top:260px;width:26px;height:26px;border:1.5px solid #fff;border-radius:50%}
.footer h4{position:absolute;top:90px;font-family:"Krona One",sans-serif;font-size:14px;color:#fff;letter-spacing:1px;font-weight:400}
.footer ul{position:absolute;list-style:none;font-size:12.5px;color:#a9adb3;letter-spacing:1px;line-height:17px}
.footer .rule{left:103px;top:326px;width:994px;height:1px;background:#444a52}
.footer .copy{top:360px;font-size:13px;color:#c9ccd1}
</style>
</head>
<body>

<header class="section site-header">
  <div class="abs brand">Rimwell<small>Works</small></div>
  <nav class="abs nav">
    <span style="left:0">Services ▾</span>
    <span style="left:95px">Gallery</span>
    <span style="left:177px">Our Clients</span>
    <span style="left:284px">Contact Us</span>
  </nav>
  <div class="abs call">
    <svg width="26" height="26" viewBox="0 0 24 24" fill="none" stroke="var(--blue-mid)" stroke-width="2"><path d="M22 16.9v3a2 2 0 0 1-2.2 2 19.8 19.8 0 0 1-8.6-3.1 19.5 19.5 0 0 1-6-6A19.8 19.8 0 0 1 2.1 4.2 2 2 0 0 1 4.1 2h3a2 2 0 0 1 2 1.7c.1.9.4 1.8.7 2.7a2 2 0 0 1-.5 2.1L8 9.8a16 16 0 0 0 6 6l1.3-1.3a2 2 0 0 1 2.1-.4c.9.3 1.8.6 2.7.7a2 2 0 0 1 1.7 2z"/></svg>
    <span class="label">Call Us!</span>
    <span class="num">(406) 555-0187</span>
  </div>
</header>

<section class="section hero">
  <div class="abs hero-photo" role="img" aria-label="Smiling mechanic fitting an alloy wheel with an impact wrench"></div>
  <div class="abs hero-welcome">WELCOME TO</div>
  <div class="abs brand hero-brand">Rimwell</div>
  <div class="abs hero-brand-sub">WORKS</div>
  <div class="abs hero-tag">Your Premier Alloy Wheel Repair Specialists</div>
  <div class="btn" style="left:119px;top:477px;width:203px;height:38px">Get a Free Quote</div>
</section>

<section class="section services">
  <div class="abs eyebrow center">Services</div>
  <h2 class="abs display center">What We Do</h2>

  <article class="card" style="left:163px">
    <svg width="80" height="80" viewBox="0 0 80 80" fill="none" stroke="var(--ink)" stroke-width="3"><circle cx="40" cy="40" r="36"/><circle cx="40" cy="40" r="28"/><circle cx="40" cy="40" r="6"/><path d="M40 12v22M40 46v22M12 40h22M46 40h22M20 20l16 16M44 44l16 16M60 20L44 36M36 44L20 60"/></svg>
    <h3>Wheel Rim<br>Refinishing</h3>
    <p>Restore damaged or corroded wheel rims to their original condition through sanding, filling, and painting.</p>
    <div class="more">READ MORE ⟶</div>
  </article>

  <article class="card featured" style="left:465px">
    <svg width="80" height="80" viewBox="0 0 80 80" fill="none" stroke="var(--blue-soft)" stroke-width="3"><rect x="30" y="14" width="20" height="52" rx="3"/><path d="M8 40h64M16 30v20M64 30v20M40 6v8M40 66v8"/></svg>
    <h3>Wheel Straightening and Balancing</h3>
    <p style="top:214px">Correct bent or misaligned wheels for improved safety, tire wear, and vehicle stability.</p>
    <div class="more">READ MORE ⟶</div>
  </article>

  <article class="card" style="left:767px">
    <svg width="80" height="80" viewBox="0 0 80 80" fill="none" stroke="var(--ink)" stroke-width="3"><path d="M30 30h26l4 10H26zM40 40v12h8v22h-8M48 20l10-10 8 8-10 10"/><path d="M14 20h6M10 28h8M14 36h6" stroke="var(--blue-mid)"/></svg>
    <h3>Custom Wheel Painting and Powder Coating</h3>
    <p style="top:214px">Personalize wheels with custom colors and finishes, adding style and durability.</p>
    <div class="more">READ MORE ⟶</div>
  </article>

  <div class="btn" style="left:495px;top:575px;width:207px;height:40px">Get a Free Quote</div>
</section>

<section class="section mission">
  <div class="abs eyebrow center">Mission Statement</div>
  <h2 class="abs display center">Restore &amp; Improve</h2>

  <div class="point" style="left:163px">
    <div class="tick"><svg width="52" height="52" viewBox="0 0 52 52" fill="none" stroke="#fff" stroke-width="4"><path d="M15 27l7 7 15-15"/></svg></div>
    <h3>RENEW AESTHETIC APPEAL</h3>
    <p>At Rimwell Works, we revive your alloy wheels' aesthetics. Scuffs, scratches, and curb damage can mar your vehicle's look. Our experts use advanced techniques to repair and refinish your wheels, restoring their shine and your car's visual appeal.</p>
  </div>
  <div class="point" style="left:622px">
    <div class="tick"><svg width="52" height="52" viewBox="0 0 52 52" fill="none" stroke="#fff" stroke-width="4"><path d="M15 27l7 7 15-15"/></svg></div>
    <h3>BOOST SAFETY &amp; PERFORMANCE</h3>
    <p>Damaged wheels affect handling and safety. We ensure your wheels meet factory standards, enhancing safety and performance for a smoother drive. Choose Rimwell Works for top-quality wheel repairs.</p>
  </div>
</section>

<section class="section gallery">
  <div class="abs eyebrow center">Gallery</div>
  <h2 class="abs display center">Explore Our Works</h2>
  <div class="tile" style="left:163px;top:493px;background:linear-gradient(135deg,#4a4f55,#1f2226)" role="img" aria-label="Technician inspecting a tyre in the workshop"></div>
  <div class="tile" style="left:459px;top:493px;background:linear-gradient(135deg,#8a8f95,#c5c9ce)" role="img" aria-label="Alloy wheel being spray painted"></div>
  <div class="tile" style="left:755px;top:493px;background:linear-gradient(135deg,#6d7d90,#2c4a78)" role="img" aria-label="Mechanic using a tyre changer machine"></div>
  <div class="tile" style="left:163px;top:776px;background:linear-gradient(135deg,#3a3d41,#7a7f85)" role="img" aria-label="Tyre mounted on a wheel service machine"></div>
  <div class="tile" style="left:459px;top:776px;background:linear-gradient(135deg,#5b6b80,#2a3240)" role="img" aria-label="Mechanic in plaid shirt working on a wheel"></div>
  <div class="tile" style="left:755px;top:776px;background:linear-gradient(135deg,#55595e,#a7abb0)" role="img" aria-label="Gloved hands balancing a wheel"></div>
  <div class="abs view-all">VIEW ALL ⟶</div>
</section>
<div class="abs mission-photo" role="img" aria-label="Mechanic in overalls rolling a tyre with an alloy rim"></div>

<section class="section quote">
  <div class="abs eyebrow center">Request a Quote</div>
  <h2 class="abs display center">Request a<br>Personalized Quote</h2>
  <div class="abs rule"></div>
  <p class="abs center">Empower Your Decision-Making With A Detailed Quote<br>Customized To Your Unique Preferences And Requirements</p>
  <div class="btn" style="left:408px;top:318px;width:208px;height:42px">Get a Free Quote</div>
  <div class="btn btn-outline" style="left:636px;top:318px;width:143px;height:42px">Know More</div>
</section>

<section class="section testimonials">
  <div class="abs eyebrow center">Testimonials</div>
  <h2 class="abs display center">Our Customers Say</h2>

  <article class="review" style="left:163px"><span class="mark">"</span><p>I was thoroughly impressed with the level of professionalism and attention to detail that Rimwell Works provided. Their team not only restored my alloy wheels to perfection but also took the time to explain the entire process. The results exceeded my expectations, and I couldn't be happier with the improved aesthetics and performance of my vehicle.</p></article>
  <article class="review" style="left:465px"><span class="mark">"</span><p>Rimwell Works completely transformed the look of my car! I had some deep scratches and scuffs on my alloy wheels that were driving me crazy. Their team worked their magic and made them look brand new. From the initial inquiry to the final result, their customer service was exceptional, and the quality of their work is outstanding.</p></article>
  <article class="review" style="left:767px"><span class="mark">"</span><p>I was amazed at how quickly Rimwell Works repaired my bent alloy wheel. I thought I might need to replace it, but their expert technicians had it back in shape in no time. It's great to know there's a reliable and efficient wheel repair service like theirs! They not only fixed my wheel but also took the time to explain the process.</p></article>

  <div class="reviewer" style="left:226px"><div class="avatar" role="img" aria-label="Customer portrait"></div><span class="name">NORA P.</span><span class="stars">★★★★★</span></div>
  <div class="reviewer" style="left:527px"><div class="avatar" role="img" aria-label="Customer portrait"></div><span class="name">DEREK L.</span><span class="stars">★★★★★</span></div>
  <div class="reviewer" style="left:827px"><div class="avatar" role="img" aria-label="Customer portrait"></div><span class="name">HANNA V.</span><span class="stars">★★★★★</span></div>

  <div class="abs dots"><span style="left:0"></span><span style="left:34px;background:var(--accent)"></span><span style="left:68px"></span></div>
</section>

<section class="section contact">
  <div class="abs contact-photo" role="img" aria-label="Mechanic kneeling beside an alloy wheel in a garage"></div>
  <div class="abs eyebrow">Contact Us</div>
  <h2 class="abs display">Get in Touch<br>With Us</h2>
  <div class="field" style="left:640px;top:218px;width:224px;height:38px"><label style="top:0">First Name <em>*</em></label></div>
  <div class="field" style="left:880px;top:218px;width:217px;height:38px"><label style="top:0">Last Name <em>*</em></label></div>
  <div class="field" style="left:640px;top:278px;width:224px;height:38px"><label style="top:0">Email Address <em>*</em></label></div>
  <div class="field" style="left:880px;top:278px;width:217px;height:38px"><label style="top:0">Phone Number <em>*</em></label></div>
  <div class="field" style="left:640px;top:338px;width:457px;height:77px"><label style="top:0">How we can help you <em>*</em></label></div>
  <div class="btn" style="left:644px;top:445px;width:111px;height:40px">Submit</div>
</section>

<footer class="section footer">
  <div class="abs brand">Rimwell<small>WORKS</small></div>
  <p class="abs about">we're dedicated to excellence in wheel repair, enhancing your vehicle's aesthetics and safety.</p>
  <span class="social" style="left:108px"></span>
  <span class="social" style="left:146px"></span>
  <span class="social" style="left:182px"></span>

  <h4 style="left:481px">USEFUL LINKS</h4>
  <ul style="left:481px;top:132px"><li style="margin-bottom:17px">Services</li><li style="margin-bottom:17px">Gallery</li><li style="margin-bottom:17px">Our Clients</li><li>Contact Us</li></ul>

  <h4 style="left:662px">SERVICES</h4>
  <ul style="left:662px;top:132px"><li style="margin-bottom:17px">Wheel Rim Refinishing</li><li style="margin-bottom:17px">Wheel Straightening<br>And Balancing</li><li>Custom Wheel Painting<br>And Powder Coating</li></ul>

  <h4 style="left:885px">CONTACT US</h4>
  <ul style="left:885px;top:132px">
    <li style="position:relative;padding-left:26px;margin-bottom:18px"><svg class="abs" style="left:0;top:0" width="16" height="16" viewBox="0 0 24 24" fill="var(--accent)"><path d="M12 2a7 7 0 0 0-7 7c0 5 7 13 7 13s7-8 7-13a7 7 0 0 0-7-7zm0 9.5A2.5 2.5 0 1 1 12 6a2.5 2.5 0 0 1 0 5.5z"/></svg>418 Harbor Ln.<br>Fairview, Illinois 85490</li>
    <li style="position:relative;padding-left:26px;margin-bottom:18px"><svg class="abs" style="left:0;top:0" width="16" height="16" viewBox="0 0 24 24" fill="none" stroke="var(--accent)" stroke-width="2.4"><path d="M22 16.9v3a2 2 0 0 1-2.2 2A19.8 19.8 0 0 1 2.1 4.2 2 2 0 0 1 4.1 2h3a2 2 0 0 1 2 1.7c.1.9.4 1.8.7 2.7a2 2 0 0 1-.5 2.1L8 9.8a16 16 0 0 0 6 6l1.3-1.3a2 2 0 0 1 2.1-.4c.9.3 1.8.6 2.7.7a2 2 0 0 1 1.7 2z"/></svg>(406) 555-0187</li>
    <li style="position:relative;padding-left:26px"><svg class="abs" style="left:0;top:0" width="16" height="16" viewBox="0 0 24 24" fill="var(--accent)"><path d="M2 5h20v14H2z M2 5l10 8 10-8" stroke="#1b1d21" stroke-width="1.5"/></svg>hello@rimwell.example</li>
  </ul>

  <div class="abs rule"></div>
  <p class="abs center copy">© 2023 All Rights Reserved | Rimwell Works</p>
</footer>

</body>
</html>
```